Business card for my new company (Accounting firm)

I need a business card for my new business Brightwell Advisory and Ledger SA. Our services are accounting, tax, audit and financial management. Our customers are small companies, start-ups and new companies. The final design has to show financial security, trust and growth. Please find our logo attached to the business card. Text for the business card: Brightwell Advisory and Ledger SA Tomas Varenholt Director and Founder Certified Accountant Tel. 022 418 57 34 tv@clairevalconseil.ch www.clairevalconseil.ch Rue des Vergières 27 1201 Geneva
Target Market(s)
Our customers are small companies, start-ups and new companies.
Industry/Entity Type
Finance And Accounting
Contact Information for Business Card
Claireval Conseil et Comptes SA
Tomas Varenholt
Directeur et Fondateur
Expert-comptable diplômé
Tél. 022 418 57 34
tv@clairevalconseil.ch
www.clairevalconseil.ch
Rue des Vergières 27
1201 Genève

```html
<!DOCTYPE html>
<html lang="en">
<head>
<meta charset="UTF-8">
<title>Claireval Conseil et Comptes SA — Business Card</title>
<link rel="stylesheet" href="https://fonts.googleapis.com/css2?family=Lato:wght@400;700&display=swap">
<style>
  :root {
    --backdrop: #e9ebee;
    --card-white: #f7f7f8;
    --panel-blue: #1a6396;
    --accent-blue: #2a9fd8;
    --ink-dark: #3a3b3d;
    --ink-light: #ffffff;
  }
  * { margin: 0; padding: 0; box-sizing: border-box; }
  html, body {
    width: 1200px;
    height: 900px;
    overflow: hidden;
    background: var(--backdrop);
    font-family: "Lato", sans-serif;
  }
  .canvas {
    width: 1200px;
    height: 900px;
    display: flex;
    align-items: center;
    justify-content: center;
  }
  .business-card {
    position: relative;
    width: 900px;
    height: 560px;
    display: flex;
    box-shadow: 0 10px 30px rgba(0,0,0,0.15);
  }
  .brand-side {
    width: 445px;
    height: 100%;
    background: var(--card-white);
    display: flex;
    align-items: center;
    justify-content: center;
  }
  .brand-name {
    display: flex;
    align-items: center;
    gap: 14px;
    color: var(--ink-dark);
    font-weight: 400;
    font-size: 30px;
    letter-spacing: 1px;
    line-height: 1.25;
    text-align: left;
  }
  .brand-mark {
    width: 18px;
    height: 18px;
    background: var(--panel-blue);
    flex: none;
  }
  .accent-stripe {
    width: 14px;
    height: 100%;
    background: var(--accent-blue);
    border-left: 4px solid var(--card-white);
  }
  .contact-side {
    position: relative;
    flex: 1;
    height: 100%;
    background: var(--panel-blue);
    color: var(--ink-light);
    padding: 120px 0 0 46px;
  }
  .panel-mark {
    position: absolute;
    left: -22px;
    top: 112px;
    width: 44px;
    height: 44px;
    border: 4px solid var(--ink-light);
    background: var(--accent-blue);
  }
  .person-name {
    font-weight: 700;
    font-size: 30px;
    line-height: 1.1;
  }
  .person-role {
    font-size: 25px;
    line-height: 1.3;
  }
  .contact-list {
    list-style: none;
    margin-top: 36px;
    font-size: 25px;
    line-height: 1.32;
  }
  .contact-list li {
    display: flex;
    align-items: center;
    gap: 9px;
  }
  .contact-list svg {
    width: 20px;
    height: 20px;
    flex: none;
  }
  .address {
    margin-top: 34px;
    font-style: normal;
    font-size: 25px;
    line-height: 1.3;
  }
</style>
</head>
<body>
  <main class="canvas">
    <article class="business-card">
      <section class="brand-side">
        <div class="brand-name">
          <span class="brand-mark"></span>
          <span>Claireval Conseil<br>et Comptes SA</span>
        </div>
      </section>
      <div class="accent-stripe"></div>
      <section class="contact-side">
        <span class="panel-mark"></span>
        <h1 class="person-name">SA TOMAS VARENHOLT</h1>
        <p class="person-role">Director and Founder<br>Certified Accountant</p>
        <ul class="contact-list">
          <li>
            <svg viewBox="0 0 20 20" aria-hidden="true"><path fill="#fff" d="M3 7c0-2 3-4 7-4s7 2 7 4v1.5h-3.5V7H6.5v1.5H3zM5 9.5h10l2 6.5H3z"/></svg>
            022 418 57 34
          </li>
          <li>
            <svg viewBox="0 0 20 20" aria-hidden="true"><rect x="2" y="5" width="16" height="11" fill="#fff"/><path d="M2.5 5.5 10 11l7.5-5.5" fill="none" stroke="#1a6396" stroke-width="1.5"/></svg>
            tv@clairevalconseil.ch
          </li>
          <li>
            <svg viewBox="0 0 20 20" aria-hidden="true"><circle cx="10" cy="10" r="8" fill="#fff"/><path d="M6 6c2 0 3 1 2 3s1 2 1 4M12 4c0 2 2 2 3 3M12 16c0-2 1-3 3-3" fill="none" stroke="#1a6396" stroke-width="1.6"/></svg>
            www.clairevalconseil.ch
          </li>
        </ul>
        <address class="address">Rue des Vergières 27<br>1201 Geneva</address>
      </section>
    </article>
  </main>
</body>
</html>
```